Vellisant - Quality health delivered at your door

Vellisant offers home and Community Based Services for adults who wish to continue live independently in their communities. We increase accessibility to health care, reduce health care delivery gap, reduce mortality and morbidity, reduce health while promoting healthy living in the comfort of our patients communities or homes.

We provide on site services and deliver high quality healthcare at your door. Our experienced physicians coordinate care with our certified nurse practitioners and provide chronic care management, physical therapy, rehabilitation and medications management.

Target Market(s)

Older population living in independent living facilities

Industry/Entity Type

Health Care

Contact Information for Business Card

Vellisant

Number of Pages Required

4 page

Font styles to use
Sans Serif

Colors

Designer to choose colors to be used in the design.

```html
<!DOCTYPE html>
<html lang="en">
<head>
<meta charset="utf-8">
<title>Vellisant – Quality health delivered at your door</title>
<link rel="stylesheet" href="https://fonts.googleapis.com/css2?family=Montserrat:wght@400;500;600;700;800&family=Raleway:wght@400;500;600;700&display=swap">
<style>
:root{
  --orange:#f7961c;
  --green:#3f5f17;
  --green-mid:#5b7f24;
  --ink:#2b2b2b;
  --text:#6f6f6f;
  --muted:#9a9a9a;
  --line:#e4e4e4;
  --soc:#8a8f96;
  --white:#ffffff;
}
*{margin:0;padding:0;box-sizing:border-box}
html,body{width:1200px;height:3982px;overflow:hidden;background:var(--white)}
body{position:relative;font-family:"Raleway",Arial,sans-serif;color:var(--text)}
.abs{position:absolute}

/* header */
.topline{left:0;top:0;width:1200px;height:5px;background:linear-gradient(90deg,var(--orange),var(--green-mid))}
.brand{display:flex;align-items:center;gap:12px}
.brand-mark{width:22px;height:22px;background:var(--muted);flex:none}
.brand-name{font-family:"Raleway",sans-serif;font-weight:700;font-size:26px;letter-spacing:.5px;color:var(--ink)}
.header-brand{left:100px;top:70px}
.contact-item{top:70px;display:flex;align-items:flex-start;gap:12px;font-size:13px;line-height:19px;color:var(--text)}
.ring{width:40px;height:40px;border-radius:50%;border:2px solid var(--orange);display:flex;align-items:center;justify-content:center;flex:none}
.socials{left:930px;top:78px;display:flex;gap:8px}
.soc{width:37px;height:37px;border-radius:50%;border:2px solid var(--soc)}

/* hero */
.hero{left:0;top:150px;width:1200px;height:515px;background:
  radial-gradient(ellipse at 78% 55%,#e9c9b0 0,#c9a68a 14%,rgba(120,150,80,0) 32%),
  linear-gradient(120deg,#4f7a2c 0%,#6f9a3d 35%,#8db457 55%,#4e6f26 100%)}
.hero-cut{left:0;top:140px;width:1200px;height:60px}
.hero-title{left:100px;top:325px;font-family:"Montserrat",sans-serif;font-weight:800;font-size:62px;letter-spacing:3px;color:var(--white)}
.hero-sub{left:100px;top:418px;width:600px;font-size:15px;line-height:24px;color:var(--white)}
.btn-ghost{left:100px;top:497px;width:138px;height:46px;border:2px solid var(--white);color:var(--white);font-weight:700;font-size:12px;letter-spacing:1px;display:flex;align-items:center;justify-content:center}
.slider-arrow{top:424px;width:40px;height:40px;border-radius:50%;background:rgba(255,255,255,.35);display:flex;align-items:center;justify-content:center}

/* nav */
.nav{left:0;top:665px;width:1200px;height:48px;background:var(--orange)}
.nav ul{list-style:none;display:flex;position:absolute;left:100px;top:0;height:48px}
.nav li{height:48px;padding:0 19px;display:flex;align-items:center;font-family:"Montserrat",sans-serif;font-weight:700;font-size:12px;letter-spacing:.4px;color:var(--white)}
.nav li.active{background:var(--green)}
.nav .search{position:absolute;left:1055px;top:14px}

/* section title */
.section-title{width:1200px;left:0;text-align:center;font-family:"Montserrat",sans-serif;font-weight:400;font-size:33px;letter-spacing:1.5px;color:var(--ink)}
.lead{left:250px;top:850px;width:700px;text-align:center;font-size:13.5px;line-height:27px;color:var(--text)}

/* welcome cards */
.card{top:952px;width:318px;height:418px;background:var(--white);border:1px solid var(--line);box-shadow:0 2px 6px rgba(0,0,0,.06);text-align:center}
.card-photo{height:244px}
.card h3{margin-top:34px;font-family:"Montserrat",sans-serif;font-weight:500;font-size:19px;color:var(--ink)}
.card p{margin:14px auto 0;width:250px;font-size:12.5px;line-height:20px;color:var(--muted)}
.read-more{display:inline-flex;align-items:center;gap:6px;margin-top:14px;font-size:12px;font-weight:600;color:var(--ink)}
.read-more.hot{color:var(--orange)}
.read-more i{width:12px;height:12px;border-radius:50%;background:var(--ink);display:inline-flex;align-items:center;justify-content:center}
.read-more.hot i{background:var(--orange)}

/* cta band */
.cta-band{left:0;top:1455px;width:1200px;height:380px;background:linear-gradient(100deg,#7a5236 0%,#b48060 35%,#d9aa85 55%,#a8734f 80%,#6d4a30 100%);clip-path:polygon(0 0,100% 0,100% 72%,50% 100%,0 72%)}
.cta-text{left:0;top:1540px;width:1200px;text-align:center;font-size:37px;line-height:55px;color:var(--white);font-weight:500}
.btn{background:var(--orange);color:var(--white);font-family:"Montserrat",sans-serif;font-weight:600;font-size:12.5px;letter-spacing:.8px;display:flex;align-items:center;justify-content:center}
.cta-btn{left:482px;top:1695px;width:236px;height:52px}

/* services */
.service{width:300px;text-align:center}
.svc-icon{width:138px;height:138px;border-radius:50%;margin:0 auto;display:flex;align-items:center;justify-content:center;background:var(--orange);border:5px solid var(--green)}
.svc-icon.alt{background:var(--green);border-color:var(--orange)}
.service h3{margin-top:38px;font-family:"Montserrat",sans-serif;font-weight:600;font-size:15.5px;line-height:22px;color:var(--ink)}
.service p{margin:14px auto 0;width:250px;font-size:12.5px;line-height:20px;color:var(--muted)}
.service .read-more{margin-top:18px}
.services-btn{left:484px;top:2740px;width:234px;height:50px}

/* news */
.news-band{left:0;top:2873px;width:1200px;height:705px;background:linear-gradient(115deg,#3a2a22 0%,#6b4a36 30%,#8c6a52 55%,#4b3a30 80%,#2e2420 100%);clip-path:polygon(0 0,100% 0,100% 83%,50% 100%,0 83%)}
.news-title{top:2935px;color:var(--white);font-weight:500;font-size:36px}
.news-card{top:3032px;width:318px;height:306px;background:var(--white);border-top:4px solid var(--orange);text-align:center}
.news-month{margin-top:40px;font-family:"Montserrat",sans-serif;font-size:24px;color:var(--ink)}
.news-year{font-family:"Montserrat",sans-serif;font-weight:700;font-size:46px;line-height:52px;color:var(--ink)}
.news-card p{margin:16px auto 0;width:262px;font-size:12px;line-height:20px;color:var(--muted)}

/* footer */
.footer-brand{left:100px;top:3700px}
.foot-head{font-family:"Montserrat",sans-serif;font-weight:600;font-size:14.5px;letter-spacing:.5px;color:var(--ink)}
.foot-col{top:3652px;font-size:12.5px;color:var(--text)}
.field{margin-top:20px;width:260px;height:44px;border:1px solid var(--line);padding:0 16px;display:flex;align-items:center;font-size:12px;color:var(--muted)}
.sub-btn{margin-top:12px;width:108px;height:40px;font-size:11.5px}
.foot-line{display:flex;gap:14px;align-items:flex-start;margin-top:18px;line-height:20px}
.divider{left:100px;top:3900px;width:1000px;height:1px;background:var(--line)}
.copyright{left:0;top:3932px;width:1200px;text-align:center;font-size:11.5px;color:var(--muted)}
</style>
</head>
<body>

<div class="abs topline"></div>

<!-- hero -->
<div class="abs hero" role="img" aria-label="Photograph of a smiling nurse embracing an older woman in a green garden"></div>
<svg class="abs hero-cut" width="1200" height="60" viewBox="0 0 1200 60" aria-hidden="true"><polygon points="0,0 1200,0 1200,10 600,34 0,10" fill="#fff"/></svg>

<header>
  <div class="abs brand header-brand"><span class="brand-mark"></span><span class="brand-name">Vellisant</span></div>
  <div class="abs contact-item" style="left:398px">
    <span class="ring"><svg width="16" height="18" viewBox="0 0 16 18"><path d="M8 1a6 6 0 0 0-6 6c0 4.5 6 10 6 10s6-5.5 6-10a6 6 0 0 0-6-6z" fill="none" stroke="#3f5f17" stroke-width="1.8"/><circle cx="8" cy="7" r="2" fill="#3f5f17"/></svg></span>
    <span>23GT, quis nostrud exercitation<br>ullamco laboris</span>
  </div>
  <div class="abs contact-item" style="left:678px">
    <span class="ring"><svg width="16" height="16" viewBox="0 0 16 16"><path d="M3 1.5l3 .5 1 3.5-2 1.3a9 9 0 0 0 4.2 4.2L10.5 9l3.5 1 .5 3-2 1.5C6.5 14.5 1.5 9.5 1.5 3.5z" fill="#3f5f17"/></svg></span>
    <span>(555) - 014 - 2286<br>info@vellisant-care.com</span>
  </div>
  <div class="abs socials"><span class="soc"></span><span class="soc"></span><span class="soc"></span><span class="soc"></span></div>
</header>

<div class="abs hero-title">VELLISANT</div>
<p class="abs hero-sub">Vellisant offers home and Community Based Services for adults who wish to continue live independently in their communities.</p>
<div class="abs btn-ghost">READ MORE</div>
<div class="abs slider-arrow" style="left:38px"><svg width="10" height="14" viewBox="0 0 10 14"><path d="M8 1L2 7l6 6" stroke="#fff" stroke-width="2" fill="none"/></svg></div>
<div class="abs slider-arrow" style="left:1122px"><svg width="10" height="14" viewBox="0 0 10 14"><path d="M2 1l6 6-6 6" stroke="#fff" stroke-width="2" fill="none"/></svg></div>

<nav class="abs nav">
  <ul>
    <li class="active">HOME</li>
    <li>ASSISTED LIVING</li>
    <li>SKILLED NURSING</li>
    <li>INDEPENDENT LIVING</li>
    <li>HOME&amp;COMMUNITY BASED SERVICES</li>
    <li>MORE</li>
  </ul>
  <svg class="search" width="18" height="18" viewBox="0 0 18 18"><circle cx="7.5" cy="7.5" r="5.5" fill="none" stroke="#fff" stroke-width="2.2"/><path d="M11.5 11.5l5 5" stroke="#fff" stroke-width="2.4"/></svg>
</nav>

<!-- welcome -->
<h1 class="abs section-title" style="top:788px">WELCOME TO VELLISANT</h1>
<p class="abs lead">Vellisant offers home and Community Based Services for adults who wish to continue to live independently in the comfort of their communities. We provide on site services and deliver high quality healthcare at your door.</p>

<article class="abs card" style="left:98px">
  <div class="card-photo" role="img" aria-label="Photograph of a caregiver and an older woman smiling together" style="background:linear-gradient(135deg,#7b5a45,#c59a7b 50%,#8a9c6a)"></div>
  <h3>Personal Care</h3>
  <p>Beatae quia luptas magni dolores eos qui ratione voluptate sequi nesciunt.</p>
  <span class="read-more">Read More <i><svg width="6" height="8" viewBox="0 0 6 8"><path d="M1 1l3 3-3 3" stroke="#fff" stroke-width="1.5" fill="none"/></svg></i></span>
</article>
<article class="abs card" style="left:441px">
  <div class="card-photo" role="img" aria-label="Photograph of an older man with a cane during a monitoring visit" style="background:linear-gradient(135deg,#6e8a4c,#a9b98a 45%,#3f5f8a)"></div>
  <h3>Monitoring visits</h3>
  <p>Beatae quia luptas magni dolores eos qui ratione voluptate sequi nesciunt.</p>
  <span class="read-more">Read More <i><svg width="6" height="8" viewBox="0 0 6 8"><path d="M1 1l3 3-3 3" stroke="#fff" stroke-width="1.5" fill="none"/></svg></i></span>
</article>
<article class="abs card" style="left:781px">
  <div class="card-photo" role="img" aria-label="Photograph of a nurse walking with an older woman" style="background:linear-gradient(135deg,#d9d2c6,#b8a894 50%,#6f6a5e)"></div>
  <h3>Dementia care</h3>
  <p>Beatae quia luptas magni dolores eos qui ratione voluptate sequi nesciunt.</p>
  <span class="read-more">Read More <i><svg width="6" height="8" viewBox="0 0 6 8"><path d="M1 1l3 3-3 3" stroke="#fff" stroke-width="1.5" fill="none"/></svg></i></span>
</article>

<!-- cta -->
<div class="abs cta-band" role="img" aria-label="Photograph of a young hand holding an older person's hands"></div>
<p class="abs cta-text">We provide on site services and deliver high<br>quality healthcare at your door</p>
<div class="abs btn cta-btn">CONTACT US NOW !</div>

<!-- services -->
<h2 class="abs section-title" style="top:1937px">OUR SERVICES</h2>

<div class="abs service" style="left:116px;top:2025px">
  <div class="svc-icon"><svg width="60" height="60" viewBox="0 0 60 60" fill="none" stroke="#fff" stroke-width="4" stroke-linecap="round"><path d="M14 8v16a10 10 0 0 0 20 0V8"/><path d="M24 34v6a12 12 0 0 0 24 0v-6"/><circle cx="48" cy="29" r="5"/></svg></div>
  <h3>Comprehensive primary<br>care services</h3>
  <p>Lorem ipsum dolor sit amet, consectetur adipisicing elit sed do eiusmod tempor.</p>
  <span class="read-more">Read More <i><svg width="6" height="8" viewBox="0 0 6 8"><path d="M1 1l3 3-3 3" stroke="#fff" stroke-width="1.5" fill="none"/></svg></i></span>
</div>
<div class="abs service" style="left:448px;top:2025px">
  <div class="svc-icon alt"><svg width="60" height="60" viewBox="0 0 60 60" fill="none" stroke="#fff" stroke-width="4" stroke-linecap="round"><rect x="10" y="14" width="40" height="32" rx="4"/><path d="M18 26h24M18 34h16"/></svg></div>
  <h3>Social services<br>assessment</h3>
  <p>Lorem ipsum dolor sit amet, consectetur adipisicing elit sed do eiusmod tempor.</p>
  <span class="read-more hot">Read More <i><svg width="6" height="8" viewBox="0 0 6 8"><path d="M1 1l3 3-3 3" stroke="#fff" stroke-width="1.5" fill="none"/></svg></i></span>
</div>
<div class="abs service" style="left:781px;top:2025px">
  <div class="svc-icon"><svg width="60" height="60" viewBox="0 0 60 60"><path d="M30 10L8 30h6v20h12V38h8v12h12V30h6z" fill="#fff"/></svg></div>
  <h3>Home health assistance</h3>
  <p>Lorem ipsum dolor sit amet, consectetur adipisicing elit sed do eiusmod tempor.</p>
  <span class="read-more">Read More <i><svg width="6" height="8" viewBox="0 0 6 8"><path d="M1 1l3 3-3 3" stroke="#fff" stroke-width="1.5" fill="none"/></svg></i></span>
</div>

<div class="abs service" style="left:116px;top:2373px">
  <div class="svc-icon"><svg width="60" height="60" viewBox="0 0 60 60"><rect x="8" y="34" width="44" height="8" rx="3" fill="#fff"/><rect x="12" y="42" width="4" height="10" fill="#fff"/><rect x="44" y="42" width="4" height="10" fill="#fff"/><circle cx="18" cy="26" r="5" fill="#fff"/><rect x="26" y="24" width="22" height="7" rx="3" fill="#fff"/></svg></div>
  <h3>Physical therapy</h3>
  <p>Lorem ipsum dolor sit amet, consectetur adipisicing elit sed do eiusmod tempor.</p>
  <span class="read-more">Read More <i><svg width="6" height="8" viewBox="0 0 6 8"><path d="M1 1l3 3-3 3" stroke="#fff" stroke-width="1.5" fill="none"/></svg></i></span>
</div>
<div class="abs service" style="left:448px;top:2373px">
  <div class="svc-icon alt"><svg width="60" height="60" viewBox="0 0 60 60" fill="none" stroke="#fff" stroke-width="4" stroke-linecap="round"><path d="M30 52v-8M30 44a16 16 0 1 1 0-32a16 16 0 0 1 0 32z"/><path d="M30 20v16M22 28h16"/></svg></div>
  <h3>Mental health</h3>
  <p>Lorem ipsum dolor sit amet, consectetur adipisicing elit sed do eiusmod tempor.</p>
  <span class="read-more hot">Read More <i><svg width="6" height="8" viewBox="0 0 6 8"><path d="M1 1l3 3-3 3" stroke="#fff" stroke-width="1.5" fill="none"/></svg></i></span>
</div>
<div class="abs service" style="left:781px;top:2373px">
  <div class="svc-icon"><svg width="60" height="60" viewBox="0 0 60 60"><path d="M18 10c-8 0-10 8-9 14 1 5 4 8 5 14s2 14 6 14 4-12 10-12 6 12 10 12 5-8 6-14 4-9 5-14c1-6-1-14-9-14-5 0-7 3-12 3s-7-3-12-3z" fill="#fff"/></svg></div>
  <h3>Dental health</h3>
  <p>Lorem ipsum dolor sit amet, consectetur adipisicing elit sed do eiusmod tempor.</p>
  <span class="read-more">Read More <i><svg width="6" height="8" viewBox="0 0 6 8"><path d="M1 1l3 3-3 3" stroke="#fff" stroke-width="1.5" fill="none"/></svg></i></span>
</div>

<div class="abs btn services-btn">VIEW ALL SERVICES</div>

<!-- news -->
<div class="abs news-band" role="img" aria-label="Photograph of a caregiver hugging an older woman in a wheelchair"></div>
<h2 class="abs section-title news-title">OUR LATEST NEWS</h2>

<article class="abs news-card" style="left:98px">
  <div class="news-month">MARCH</div><div class="news-year">2017</div>
  <p>Sed ut perspiciatis unde omnis iste natus error sit voluptatem accusantium doloremque laudantium, totam rem aperiam eaque ipsa quae.</p>
  <span class="read-more">Read More <i><svg width="6" height="8" viewBox="0 0 6 8"><path d="M1 1l3 3-3 3" stroke="#fff" stroke-width="1.5" fill="none"/></svg></i></span>
</article>
<article class="abs news-card" style="left:441px">
  <div class="news-month">JUNE</div><div class="news-year">2017</div>
  <p>Sed ut perspiciatis unde omnis iste natus error sit voluptatem accusantium doloremque laudantium, totam rem aperiam eaque ipsa quae.</p>
  <span class="read-more">Read More <i><svg width="6" height="8" viewBox="0 0 6 8"><path d="M1 1l3 3-3 3" stroke="#fff" stroke-width="1.5" fill="none"/></svg></i></span>
</article>
<article class="abs news-card" style="left:781px">
  <div class="news-month">JULY</div><div class="news-year">2017</div>
  <p>Sed ut perspiciatis unde omnis iste natus error sit voluptatem accusantium doloremque laudantium, totam rem aperiam eaque ipsa quae.</p>
  <span class="read-more">Read More <i><svg width="6" height="8" viewBox="0 0 6 8"><path d="M1 1l3 3-3 3" stroke="#fff" stroke-width="1.5" fill="none"/></svg></i></span>
</article>

<!-- footer -->
<footer>
  <div class="abs brand footer-brand"><span class="brand-mark"></span><span class="brand-name">Vellisant</span></div>

  <div class="abs foot-col" style="left:330px">
    <div class="foot-head">SUBSCRIBE TO NEWSLETTER</div>
    <div style="margin-top:18px;font-size:11.5px">Eiusmod tempor incididunt ut dolore.</div>
    <div class="field">Enter Mail....</div>
    <div class="btn sub-btn">SUBSCRIBE</div>
  </div>

  <div class="abs foot-col" style="left:641px">
    <div class="foot-head">CONTACT US</div>
    <div class="foot-line"><svg width="16" height="18" viewBox="0 0 16 18"><path d="M8 1a6 6 0 0 0-6 6c0 4.5 6 10 6 10s6-5.5 6-10a6 6 0 0 0-6-6z" fill="none" stroke="#3f5f17" stroke-width="1.6"/><circle cx="8" cy="7" r="2" fill="#3f5f17"/></svg><span>23GT, quis nostrud exercition<br>ullamco laboris</span></div>
    <div class="foot-line"><svg width="16" height="16" viewBox="0 0 16 16"><path d="M3 1.5l3 .5 1 3.5-2 1.3a9 9 0 0 0 4.2 4.2L10.5 9l3.5 1 .5 3-2 1.5C6.5 14.5 1.5 9.5 1.5 3.5z" fill="#3f5f17"/></svg><span>(555) - 014 - 2286</span></div>
    <div class="foot-line"><svg width="18" height="14" viewBox="0 0 18 14"><rect x="1" y="1" width="16" height="12" fill="none" stroke="#3f5f17" stroke-width="1.6"/><path d="M1 1l8 7 8-7" fill="none" stroke="#3f5f17" stroke-width="1.6"/></svg><span>info@vellisant-care.com</span></div>
  </div>

  <div class="abs foot-col" style="left:928px">
    <div class="foot-head">FOLLOW US</div>
    <div style="display:flex;gap:8px;margin-top:20px"><span class="soc"></span><span class="soc"></span><span class="soc"></span><span class="soc"></span></div>
  </div>

  <div class="abs divider"></div>
  <p class="abs copyright">© copyright 2017 Vellisant. All Rights Reserved</p>
</footer>

</body>
</html>
```